Need a new company business card

I am looking for a new company business card. Front and back. With information on it as per below. Card should be professional. Yet clever. Simple. Modern design. Pim card, traditional size. OK with say, all black or all red backside.

Varnholt is an indie, bootstrapped magazine advancing the work of intersectional feminists busting their buts to create a just world through the power of enterprise and innovation.

Varnholt is the home and voice of entrepreneurial feminism and feminist innovators worldwide. Entrepreneurial feminists are people (of all genders) who see inequality as an innovation priority. They work to advance gender equity and/or who strive to integrate and practice feminist principles, pedagogy, values into their innovation and entrepreneurship work.
We are committed to this space being trans and queer inclusive, anti-racist, intersectional, brave, and safe. We welcome all allies. We value learning, edgy but civil discourse and integrative thinking skills.

Target Market(s)

feminists, business owners,

Industry/Entity Type

Publishing Company

Contact Information for Business Card

RD Tolliver
Founder/Publisher
4-237 Ashgrove Lane, Toronto, ON
M4T 2K8
publisher@varnholt.com
416-552-3019
www.varnholt.com

Font styles to use
Serif
Other font styles liked:
• Myriad Pro

Colors
ec1f27
000000
ffffff

Requirements
Must have
• logo
• use red, black white colours only.
Nice to have
• use the compass in pattern or creatively but not too busy please
Should not have
• Should not be too busy. Elegant.

```html
<!DOCTYPE html>
<html lang="en">
<head>
<meta charset="utf-8">
<title>Varnholt business card</title>
<link rel="stylesheet" href="https://fonts.googleapis.com/css2?family=Roboto:wght@400;700&family=Roboto+Condensed:wght@400;700&family=Source+Sans+3:wght@700&display=swap">
<style>
  :root {
    --brand-red: #ec1f27;
    --ink: #222222;
    --ink-soft: #555555;
    --paper: #ffffff;
    --backdrop: #e9e7e4;
  }
  * { box-sizing: border-box; margin: 0; padding: 0; }
  html, body { width: 1200px; height: 886px; overflow: hidden; }
  body {
    background: var(--backdrop);
    font-family: "Roboto", Arial, sans-serif;
    position: relative;
  }
  .card {
    position: absolute;
    left: 320px;
    width: 560px;
    height: 320px;
    border-radius: 3px;
    box-shadow: 0 6px 18px rgba(0,0,0,0.18);
    overflow: hidden;
  }
  .card-front { top: 93px; background: var(--brand-red); }
  .card-back { top: 473px; background: var(--paper); }

  .front-texture {
    position: absolute; inset: 0;
    background: var(--brand-red);
  }
  .wordmark {
    font-family: "Source Sans 3", "Myriad Pro", Arial, sans-serif;
    font-weight: 700;
    letter-spacing: -1px;
    line-height: 1;
    position: absolute;
  }
  .card-front .wordmark {
    color: var(--paper);
    font-size: 84px;
    left: 0; right: 0; top: 118px;
    text-align: center;
  }
  .card-back .wordmark {
    color: var(--ink);
    font-size: 58px;
    left: 38px; top: 72px;
  }

  .name-band {
    position: absolute;
    right: 0; top: 64px;
    width: 200px; height: 58px;
    background: var(--brand-red);
    clip-path: polygon(0 0, 100% 0, 100% 100%, 0 100%, 14px 50%);
    color: var(--paper);
    font-family: "Roboto Condensed", Arial, sans-serif;
    padding: 9px 0 0 40px;
  }
  .person-name { font-weight: 700; font-size: 20px; line-height: 1.05; text-transform: uppercase; }
  .person-title { font-size: 14px; line-height: 1.3; }

  .contact {
    position: absolute;
    left: 38px; bottom: 34px;
    color: var(--ink-soft);
    font-size: 13px;
    line-height: 1.45;
  }
  .address { margin-bottom: 8px; }
  .contact-row { display: flex; align-items: center; gap: 8px; }
  .contact-row svg { width: 11px; height: 11px; fill: var(--ink); flex: none; }
</style>
</head>
<body>

<section class="card card-front" aria-label="Card front">
  <div class="front-texture" role="img" aria-label="Subtle repeating tonal pattern in brand red"></div>
  <div class="wordmark">Varnholt</div>
</section>

<section class="card card-back" aria-label="Card back">
  <div class="wordmark">Varnholt</div>

  <div class="name-band">
    <div class="person-name">RD Tolliver</div>
    <div class="person-title">Founder/Publisher</div>
  </div>

  <div class="contact">
    <div class="address">4-237 Ashgrove Lane<br>Toronto, ON, M4T 2K8</div>
    <div class="contact-row">
      <svg viewBox="0 0 24 24" aria-hidden="true"><path d="M6.6 10.8a15.1 15.1 0 0 0 6.6 6.6l2.2-2.2a1 1 0 0 1 1-.25 11.4 11.4 0 0 0 3.6.57 1 1 0 0 1 1 1V20a1 1 0 0 1-1 1A17 17 0 0 1 3 4a1 1 0 0 1 1-1h3.5a1 1 0 0 1 1 1c0 1.25.2 2.45.57 3.57a1 1 0 0 1-.25 1z"/></svg>
      <span>416-552-3019</span>
    </div>
    <div class="contact-row">
      <svg viewBox="0 0 24 24" aria-hidden="true"><path d="M2 5h20v14H2z M4 7v.5l8 5 8-5V7l-8 5z" fill-rule="evenodd"/></svg>
      <span>publisher@varnholt.com</span>
    </div>
    <div class="contact-row">
      <svg viewBox="0 0 24 24" aria-hidden="true"><circle cx="12" cy="12" r="10"/><path d="M2 12h20M12 2c3 3 3 17 0 20M12 2c-3 3-3 17 0 20" stroke="#fff" stroke-width="1.5" fill="none"/></svg>
      <span>www.varnholt.com</span>
    </div>
  </div>
</section>

</body>
</html>
```